Website Performance Testing eBook for the software testing industry

Overview:
I would like an ebook/whitepaper designed. This ebook will be digital published on my website as a lead generation piece. The purpose is to give high level tips on what to look for and things to think about when working on a website performance testing project.
The ebook also demonstrates our expertise and knowledge on the topic.
Topic:
This is an ebook on software testing. Specifically, website performance testing.
About Veltrana:
Veltrana Solutions is an outsourcing development and software testing firm, and we provide expert services for application development, testing and data analytics. We extend our clients’ software testing capabilities with on-demand technical expertise. Our quality assurance resources work as part of our clients’ teams to help test applications on time and within budget.
Our model is designed to allocate the right mix of local and offshore resources in order to optimize expertise, speed and cost. We provide the ability to quickly add specialty skills to our client’s development team without them incurring long-term costs. The result is far better management of resource capacities and outcomes.
Background on our branding and previous pieces:
I have included a few of our previous ebooks and whitepapers. I like the look and feel of these pieces, however we have made updates to our brand guidelines since them, so the new brand guidelines will need to be incorporated, and I'd like to refresh/update what we have done in the past.
Refer to our website for an idea of our look and feel. This page is one of our newer sections and would be a good reference:
http://www.veltranasol.example/data-analytics/
Tone and feel:
- The look and feel should be professional, clean and polished.
- I like good use of whitespace.
- I would prefer to keep stock photography of people to a minimum. Any images should add to the content and be relevant to the content.
(Also, I uploaded some InDesign files in case you wanted to refer to those assets, but I didn't include the Links folder because they were too big. If there's anything you more you need, let me know)
Target Market(s)
Audience:
The audience is senior Quality Assurance and Software Testing professionals.
- 30-45 years old
- Technical mindset
- Interested in learning
Titles include
- QA Lead
- QA Manager
- QA Director
- Director or VP of Development
- QA Automation Engineer
Our customers are medium to large sized companies. Many are software companies, but many are also enterprises in all almost all industries.

```html
<!DOCTYPE html>
<html lang="en">
<head>
<meta charset="UTF-8">
<title>Website Performance Testing – Types of Performance Testing</title>
<link rel="stylesheet" href="https://fonts.googleapis.com/css2?family=Open+Sans:wght@300;400;600&display=swap">
<style>
  :root {
    --brand-red: #e8372c;
    --rule-grey: #d4d4d4;
    --text-grey: #5b5b5b;
    --heading-grey: #b3b6bb;
    --page-bg: #ffffff;
  }
  * { margin: 0; padding: 0; box-sizing: border-box; }
  html, body {
    width: 927px;
    height: 1200px;
    overflow: hidden;
    background: var(--page-bg);
  }
  .page {
    position: relative;
    width: 927px;
    height: 1200px;
    font-family: "Open Sans", Arial, sans-serif;
    color: var(--text-grey);
  }
  .running-head {
    position: absolute;
    left: 54px;
    top: 73px;
    font-size: 13px;
    font-weight: 400;
    color: var(--text-grey);
  }
  .brand-name {
    position: absolute;
    right: 65px;
    top: 68px;
    font-size: 18px;
    font-weight: 400;
    color: var(--brand-red);
  }
  .header-rule {
    position: absolute;
    left: 54px;
    top: 109px;
    width: 818px;
    height: 1px;
    background: var(--rule-grey);
  }
  .title-bar {
    position: absolute;
    left: 97px;
    top: 166px;
    width: 2px;
    height: 106px;
    background: var(--brand-red);
  }
  .section-title {
    position: absolute;
    left: 125px;
    top: 193px;
    font-size: 41px;
    font-weight: 300;
    color: var(--brand-red);
    letter-spacing: 0.2px;
    line-height: 1.2;
  }
  .copy {
    position: absolute;
    left: 109px;
    width: 722px;
    font-size: 15.4px;
    font-weight: 400;
    line-height: 21.2px;
  }
  .copy-intro { top: 322px; }
  .copy-intro .last-line { display: inline-block; margin-top: 6px; }
  .copy-baseline { top: 480px; }
  .copy-lead { top: 595px; }
  .copy-load { top: 745px; }
  .copy-stress { top: 964px; }
  .subheading {
    position: absolute;
    left: 109px;
    font-size: 24px;
    font-weight: 600;
    color: var(--heading-grey);
    letter-spacing: 0.3px;
  }
  .subheading-load { top: 667px; }
  .subheading-stress { top: 886px; }
  .page-number {
    position: absolute;
    left: 817px;
    top: 1123px;
    font-size: 16px;
    font-weight: 300;
    color: var(--brand-red);
  }
</style>
</head>
<body>
<div class="page">
  <header>
    <div class="running-head">Website Performance Testing</div>
    <div class="brand-name">Veltrana Solutions</div>
    <div class="header-rule"></div>
  </header>

  <div class="title-bar"></div>
  <h1 class="section-title">TYPES OF PERFORMANCE TESTING</h1>

  <p class="copy copy-intro">Performance testing assesses your site’s efficiency compared to its specifications. Its main focus is overall responsiveness under average loads. This category of testing should be performed early and often in order to uncover imbalances in the software architecture or its implementation. Monopolization of resources, processing bottlenecks and unexpected latency are likely suspects, which are easier to correct <span class="last-line">early on rather than at later stages in development or testing.</span></p>

  <p class="copy copy-baseline">The end result of these performance tests and subsequent software changes is a set of baseline measurements you apply whenever the web site is changed to ensure that responsiveness and processing efficiency are stable and improving.</p>

  <p class="copy copy-lead">Let us look at two specific types of website performance testing: Load Testing and Stress Testing.</p>

  <h2 class="subheading subheading-load">LOADING TESTING</h2>
  <p class="copy copy-load">After early performance test results stabilizes, load tests that simulate thousands or even millions of users over long time periods are appropriate for measuring software endurance and volume capacity. These take you one step closer to real-world conditions. These tests uncover buffer overflows, memory leaks, and responsiveness degradation.</p>

  <h2 class="subheading subheading-stress">STRESS TESTING</h2>
  <p class="copy copy-stress">Stress tests apply maximum burden on the website in order to uncover its breaking points. Equally important, these tests measure how gracefully your site crashes and recovers. Success is declared when the site can fail without losing data, does not create security risks and recovers quickly with minimal disruption to users.</p>

  <div class="page-number">2</div>
</div>
</body>
</html>
```